Name of business TRV Harbor Asset Partners, LP.
business focuses on hotel investments and real estate deals, on the bottom of the card I need my partner company listed as "Strategic Partner of Velmora Lodging Group" www.velmoralodginggroup-example.com and the logo that is attached for them on the bottom also

I am the Principal of the business

Industry/Entity Type

Real Estate

Contact Information for Business Card

Devin Marsh
287 Quarry Lane
Cedar Hollow, TN 00000
C- 555-302-1846
D- 555-719-2063
F- 555-864-3371

```html
<!DOCTYPE html>
<html lang="en">
<head>
<meta charset="utf-8">
<title>TRV Harbor Asset Partners – Business Card</title>
<link rel="stylesheet" href="https://fonts.googleapis.com/css2?family=Montserrat:wght@400;500;700&display=swap">
<style>
  :root {
    --slate: #3e5166;
    --paper: #ffffff;
    --navy: #1b1f6e;
    --brand-blue: #29a8df;
    --backdrop: #e4e6ea;
    --shadow: rgba(20, 30, 45, 0.25);
  }
  * { margin: 0; padding: 0; box-sizing: border-box; }
  html, body {
    width: 1200px;
    height: 1000px;
    overflow: hidden;
    background: var(--backdrop);
    font-family: "Montserrat", Arial, sans-serif;
  }
  .card {
    position: absolute;
    left: 100px;
    top: 210px;
    width: 1000px;
    height: 580px;
    background: var(--paper);
    box-shadow: 0 14px 40px var(--shadow);
    overflow: hidden;
  }
  .card-shapes { position: absolute; inset: 0; }
  .card-shapes .panel { fill: var(--slate); }
  .card-shapes .strip { fill: var(--paper); }

  .holder-name {
    position: absolute;
    left: 215px;
    top: 165px;
    font-size: 40px;
    font-weight: 700;
    color: var(--navy);
    letter-spacing: 0.5px;
    white-space: nowrap;
  }
  .phone {
    position: absolute;
    left: 382px;
    font-size: 22px;
    line-height: 38px;
    font-weight: 500;
    color: var(--navy);
    white-space: nowrap;
  }
  .phone-cell { top: 245px; }
  .phone-direct { top: 298px; }
  .phone-fax { top: 351px; }

  .company {
    position: absolute;
    left: 50px;
    top: 472px;
    color: var(--paper);
    font-size: 23px;
    line-height: 34px;
    font-weight: 400;
    white-space: nowrap;
  }

  .partner-mark {
    position: absolute;
    left: 668px;
    top: 174px;
    display: flex;
    align-items: center;
    gap: 12px;
    white-space: nowrap;
  }
  .partner-mark .dot {
    width: 40px;
    height: 40px;
    border-radius: 50%;
    background: var(--navy);
    flex: none;
  }
  .partner-mark .partner-name {
    font-size: 20px;
    font-weight: 700;
    color: var(--brand-blue);
  }

  .partner-info {
    position: absolute;
    left: 650px;
    right: 0;
    top: 425px;
    text-align: center;
    color: var(--paper);
    font-size: 13px;
    line-height: 30px;
    white-space: nowrap;
  }
</style>
</head>
<body>
  <div class="card">
    <svg class="card-shapes" width="1000" height="580" viewBox="0 0 1000 580" aria-hidden="true">
      <polygon class="panel" points="0,0 600,0 625,580 0,580"/>
      <polygon class="panel" points="645,360 1000,360 1000,580 655,580"/>
      <rect class="strip" x="0" y="150" width="609" height="76"/>
      <rect class="strip" x="360" y="245" width="254" height="38"/>
      <rect class="strip" x="360" y="298" width="256" height="38"/>
      <rect class="strip" x="360" y="351" width="258" height="38"/>
    </svg>

    <div class="holder-name">Devin Marsh</div>

    <div class="phone phone-cell">C : 555-302-1846</div>
    <div class="phone phone-direct">D : 555-719-2063</div>
    <div class="phone phone-fax">F : 555-864-3371</div>

    <div class="company">
      <p>TRV Harbor Asset Partners, LP.</p>
      <p>287 Quarry Lane Cedar Hollow, TN 00000</p>
    </div>

    <div class="partner-mark">
      <span class="dot"></span>
      <span class="partner-name">Velmora Lodging Group</span>
    </div>

    <div class="partner-info">
      <p>"Strategic Partner of Velmora Lodging Group"</p>
      <p>www.velmoralodginggroup-example.com</p>
    </div>
  </div>
</body>
</html>
```